Kelo Wave Mint Business cards

Logo, tag line and photo on card
Agent Name
Title
Address
Phone number
Email
Website
Make logo on one side large by rotating  to portrait format.  Keep the background of the logo white.

Contact Information for Business Card
Slogan; Making Every Wave Count

```html
<!DOCTYPE html>
<html lang="en">
<head>
<meta charset="utf-8">
<title>Kelo Wave Mint – Business Cards</title>
<link href="https://fonts.googleapis.com/css2?family=Montserrat:wght@800&family=Open+Sans:wght@400;600&display=swap" rel="stylesheet">
<style>
  :root{
    --stage:#222222;
    --navy:#21306a;
    --red:#c4202b;
    --white:#ffffff;
    --ink:#1c1c1c;
    --wave-1:#ececec;
    --wave-2:#d6d6d6;
    --photo:#2a2a2a;
  }
  *{margin:0;padding:0;box-sizing:border-box}
  html,body{width:1200px;height:711px;overflow:hidden;background:var(--stage)}
  .stage{position:relative;width:1200px;height:711px}
  .card{position:absolute;top:76px;width:320px;height:560px;border-radius:22px;overflow:hidden}
  .card--front{left:250px;background:var(--navy)}
  .card--back{left:630px;background:var(--white)}

  .brand-box{position:absolute;left:34px;top:140px;width:252px;height:280px;background:var(--white);
    border:9px solid var(--red);border-radius:24px;display:flex;align-items:center;justify-content:center}
  .brand-name{font-family:"Montserrat",sans-serif;font-weight:800;color:var(--navy);
    font-size:58px;line-height:1.02;text-align:center;letter-spacing:-1px}

  .brand-box--small{left:112px;top:24px;width:96px;height:96px;border-width:3px;border-radius:9px}
  .brand-box--small .brand-name{font-size:20px;letter-spacing:-.4px}

  .portrait{position:absolute;left:104px;top:132px;width:112px;height:112px;border-radius:50%;
    border:3px solid var(--red);background:radial-gradient(circle at 50% 45%,#6b5a50 0%,#3b3633 45%,var(--photo) 75%)}

  .waves{position:absolute;left:0;bottom:0;width:320px;height:100px;z-index:0}

  .agent{position:absolute;left:0;right:0;top:252px;text-align:center;z-index:1}
  .agent-name{font-family:"Montserrat",sans-serif;font-weight:800;color:var(--red);font-size:25px;line-height:1.2}
  .agent-title{font-family:"Open Sans",sans-serif;font-weight:600;color:var(--ink);font-size:13px;margin-top:1px}

  .icon-row{display:flex;justify-content:center;gap:6px;margin-top:7px}
  .icon{width:22px;height:22px;border-radius:50%;background:var(--red);display:flex;align-items:center;justify-content:center}
  .icon svg{width:13px;height:13px}

  .contact{font-family:"Open Sans",sans-serif;color:var(--ink);font-size:13.5px;line-height:1.4;margin-top:5px}
  .pin{margin:8px auto 4px}
  .address{font-family:"Open Sans",sans-serif;color:var(--ink);font-size:13.5px;line-height:1.35}

  .slogan{position:absolute;left:0;right:0;bottom:22px;text-align:center;z-index:1;
    font-family:"Open Sans",sans-serif;font-weight:600;color:var(--red);font-size:14px}
</style>
</head>
<body>
<main class="stage">

  <section class="card card--front" aria-label="Card front">
    <div class="brand-box">
      <p class="brand-name">Kelo<br>Wave<br>Mint</p>
    </div>
  </section>

  <section class="card card--back" aria-label="Card back">
    <div class="brand-box brand-box--small">
      <p class="brand-name">Kelo<br>Wave<br>Mint</p>
    </div>

    <div class="portrait" role="img" aria-label="Portrait photo of Daniel Roark"></div>

    <svg class="waves" viewBox="0 0 320 100" preserveAspectRatio="none" aria-hidden="true">
      <defs>
        <linearGradient id="waveShade" x1="0" y1="0" x2="0" y2="1">
          <stop offset="0" stop-color="var(--wave-2)"/>
          <stop offset="1" stop-color="var(--white)"/>
        </linearGradient>
      </defs>
      <path d="M0 28 Q170 110 320 12 L320 100 L0 100Z" fill="url(#waveShade)"/>
      <path d="M0 44 Q180 118 320 34 L320 100 L0 100Z" fill="var(--wave-1)"/>
      <path d="M0 100 Q130 50 320 58 L320 100Z" fill="var(--white)" opacity=".85"/>
    </svg>

    <div class="agent">
      <h1 class="agent-name">Daniel Roark</h1>
      <p class="agent-title">Co-Founder</p>

      <div class="icon-row">
        <span class="icon"><svg viewBox="0 0 24 24" fill="#fff"><path d="M6.6 10.8a15 15 0 0 0 6.6 6.6l2.2-2.2c.3-.3.7-.4 1-.2 1.1.4 2.3.6 3.6.6.6 0 1 .4 1 1V20c0 .6-.4 1-1 1A17 17 0 0 1 3 4c0-.6.4-1 1-1h3.5c.6 0 1 .4 1 1 0 1.3.2 2.5.6 3.6.1.3 0 .7-.2 1z"/></svg></span>
        <span class="icon"><svg viewBox="0 0 24 24" fill="none" stroke="#fff" stroke-width="2"><rect x="3" y="5" width="18" height="14" rx="2"/><path d="M3 7l9 6 9-6"/></svg></span>
        <span class="icon"><svg viewBox="0 0 24 24" fill="none" stroke="#fff" stroke-width="2"><circle cx="12" cy="12" r="9"/><path d="M3 12h18M12 3c3 3 3 15 0 18M12 3c-3 3-3 15 0 18"/></svg></span>
      </div>

      <p class="contact">(555) 214-0386<br>info@website.com<br>www.website.com</p>

      <span class="icon pin"><svg viewBox="0 0 24 24" fill="none" stroke="#fff" stroke-width="2"><path d="M12 21s-6-6.2-6-11a6 6 0 0 1 12 0c0 4.8-6 11-6 11z"/><circle cx="12" cy="10" r="2.2"/></svg></span>
      <p class="address">1480 Harbor Ln. Suite 300<br>Denton, TX 76201</p>
    </div>

    <p class="slogan">Making Every Wave Count</p>
  </section>

</main>
</body>
</html>
```